Stationary design for boutique production house

We need a stationary design for our production house, 'Lorno Productions' based in Singapore. We produce microfilms as well as podcasts, talkshows and events. Our logo is a stylized icon of our director, who is also the executive producer and host of our programs, Lorno. Our main company colors are Red, Black and white. We would like a clean, minimalist design incorporating our existing company logo that conveys a sense of urbanism and elegance.

Logo and font files are attached. f

Target Market(s)

We focus on lifestyle media rather than entertainment.

Industry/Entity Type

Boutique

Font styles to use
Serif
Sans Serif

Colors
ec1f27
ffffff
000000

Requirements
Must have
• Our company logo and at least one of our company colors.
Nice to have
• Our address and contact information.
Should not have
• Changes made to the company logo (using only certain parts of it is fine though)

```html
<!DOCTYPE html>
<html lang="en">
<head>
<meta charset="utf-8">
<title>Lorno Productions — Business Cards</title>
<link rel="stylesheet" href="https://fonts.googleapis.com/css2?family=Playfair+Display:wght@700&family=Jost:wght@400&display=swap">
<style>
  :root {
    --brand-red: #ec1f27;
    --ink: #1a1a1a;
    --ink-soft: #333333;
    --paper: #ffffff;
    --backdrop: #e9e9e9;
  }
  * { margin: 0; padding: 0; box-sizing: border-box; }
  html, body {
    width: 1200px;
    height: 768px;
    overflow: hidden;
    background: var(--backdrop);
  }
  .card {
    position: absolute;
    top: 227px;
    width: 550px;
    height: 314px;
    background: var(--paper);
    font-family: "Jost", "Helvetica Neue", Arial, sans-serif;
    color: var(--ink);
    box-shadow: 0 2px 10px rgba(0,0,0,0.08);
  }
  .card--back { left: 30px; }
  .card--front { left: 620px; }

  /* Back side: centred wordmark */
  .back-mark {
    position: absolute;
    left: 0;
    top: 0;
    width: 100%;
    height: 100%;
    display: flex;
    flex-direction: column;
    align-items: center;
    justify-content: center;
    gap: 14px;
  }
  .back-mark__dot {
    width: 16px;
    height: 16px;
    border-radius: 50%;
    background: var(--brand-red);
  }
  .back-mark__name {
    font-family: "Playfair Display", Georgia, serif;
    font-weight: 700;
    font-size: 30px;
    line-height: 1.1;
    text-align: center;
    text-transform: uppercase;
    letter-spacing: 1px;
    color: var(--ink);
  }

  /* Front side */
  .wordmark {
    position: absolute;
    left: 170px;
    top: 58px;
    width: 340px;
    text-align: center;
    font-family: "Playfair Display", Georgia, serif;
    font-weight: 700;
    text-transform: uppercase;
    color: var(--ink);
    line-height: 1;
  }
  .wordmark__line1 { display: block; font-size: 30px; letter-spacing: 1px; }
  .wordmark__line2 { display: block; font-size: 36px; margin-top: 4px; }
  .rule {
    position: absolute;
    left: 30px;
    top: 148px;
    width: 490px;
    height: 1.5px;
    background: var(--ink);
  }
  .rule__dot {
    position: absolute;
    top: -3.25px;
    width: 8px;
    height: 8px;
    border-radius: 50%;
    background: var(--brand-red);
  }
  .rule__dot--left { left: 190px; }
  .rule__dot--right { left: 380px; }
  .person {
    position: absolute;
    left: 30px;
    top: 166px;
  }
  .person__name {
    font-size: 16px;
    font-weight: 400;
    letter-spacing: 0.5px;
    text-transform: uppercase;
    line-height: 1.2;
  }
  .person__role {
    font-size: 13px;
    color: var(--brand-red);
    text-transform: uppercase;
    line-height: 1.3;
  }
  .person__address {
    margin-top: 3px;
    font-size: 12px;
    color: var(--ink-soft);
    line-height: 1.35;
    font-style: normal;
  }
  .contacts {
    position: absolute;
    right: 28px;
    bottom: 22px;
    list-style: none;
  }
  .contacts__item {
    display: flex;
    align-items: center;
    justify-content: flex-end;
    gap: 10px;
    font-size: 12.5px;
    letter-spacing: 1px;
    line-height: 19px;
    color: var(--ink-soft);
  }
  .contacts__icon {
    width: 12px;
    height: 12px;
    fill: var(--ink);
  }
</style>
</head>
<body>
  <section class="card card--back" aria-label="Card back">
    <div class="back-mark">
      <span class="back-mark__dot"></span>
      <div class="back-mark__name">Lorno<br>Productions</div>
    </div>
  </section>

  <section class="card card--front" aria-label="Card front">
    <div class="wordmark">
      <span class="wordmark__line1">Lorno</span>
      <span class="wordmark__line2">Productions</span>
    </div>
    <div class="rule">
      <span class="rule__dot rule__dot--left"></span>
      <span class="rule__dot rule__dot--right"></span>
    </div>

    <div class="person">
      <h1 class="person__name">Daniel Reyes</h1>
      <p class="person__role">CEO/Founder</p>
      <address class="person__address">214 Linden Row<br>Clarkfield, Oregon 20817</address>
    </div>

    <ul class="contacts">
      <li class="contacts__item">512 304 7716
        <svg class="contacts__icon" viewBox="0 0 24 24" aria-label="Phone"><path d="M6.6 10.8a15.1 15.1 0 0 0 6.6 6.6l2.2-2.2a1 1 0 0 1 1-.25 11.4 11.4 0 0 0 3.6.57 1 1 0 0 1 1 1V20a1 1 0 0 1-1 1A17 17 0 0 1 3 4a1 1 0 0 1 1-1h3.5a1 1 0 0 1 1 1c0 1.25.2 2.45.57 3.6a1 1 0 0 1-.25 1z"/></svg>
      </li>
      <li class="contacts__item">512 889 2043
        <svg class="contacts__icon" viewBox="0 0 24 24" aria-label="Mobile"><path d="M7 1h10a2 2 0 0 1 2 2v18a2 2 0 0 1-2 2H7a2 2 0 0 1-2-2V3a2 2 0 0 1 2-2zm0 3v15h10V4z"/></svg>
      </li>
      <li class="contacts__item">512 670 3185
        <svg class="contacts__icon" viewBox="0 0 24 24" aria-label="Fax"><path d="M6 2h10l2 2v4H6zM3 9h18a1 1 0 0 1 1 1v8h-4v4H6v-4H2v-8a1 1 0 0 1 1-1zm5 7v4h8v-4z"/></svg>
      </li>
      <li class="contacts__item">hello@lornomedia.com
        <svg class="contacts__icon" viewBox="0 0 24 24" aria-label="Email"><path d="M2 5h20v14H2zm2 2v.5l8 5 8-5V7zm0 3v7h16v-7l-8 5z"/></svg>
      </li>
    </ul>
  </section>
</body>
</html>
```